Tavenhurst Falcons FC Website

We are looking to develop a new website for Tavenhurst FC. Tavenhurst FC has now joined with Tavenhurst Falcons FC and we are looking at a website that can work for both clubs. Tavenhurst FC play in a local park football competition while tavenhurst Falcons are a Semi Professional team that plays in the Ostral Premier Series Competition. What we are after is two separate website off the one platform. I have attached both team logos for you to visualise. Also you can look at the existing tavenhurst website www.tavenhurstfc.net.au. We are looking for a huge improvement in the website and it will be imperative we have links to sponsors and the sponsors can get regular visuals. Weare looking to move this club forward and have a very professional website that can communicate clearly with the community.

Hi All,

Please remember that the website is to represent two clubs;
1. Tavenhurst Falcons FC (Competes in Semi Professional League)
2. Tavenhurst FC (Compete in KPWLT League which is a lower level)

Further to this the Tavenhurst Falcons FC page will require a player profile page which will show photos of each player and a little bio on each.

Thanks

Reason: Would like to spend more time review existing and new designs

```html
<!DOCTYPE html>
<html lang="en">
<head>
<meta charset="utf-8">
<title>Tavenhurst FC</title>
<link href="https://fonts.googleapis.com/css2?family=Exo:wght@400;500;600;700&family=Open+Sans:ital,wght@0,400;0,600;0,700;1,400&display=swap" rel="stylesheet">
<style>
:root{
  --red:#d0121b;
  --red-dark:#9c0a10;
  --ink:#222;
  --grey-text:#8a8a8a;
  --light-bg:#ececec;
  --line:#2a2a2a;
  --footer-bg:#1f1f1f;
  --footer-text:#b5b5b5;
  --yellow:#f3c500;
  --white:#fff;
}
*{margin:0;padding:0;box-sizing:border-box}
html,body{width:1200px;height:2323px;overflow:hidden}
body{position:relative;background:var(--white);font-family:"Open Sans",Arial,sans-serif;color:var(--ink)}
.abs{position:absolute}
.heading{font-family:"Exo",Arial,sans-serif;text-transform:uppercase;font-weight:500}
.red{color:var(--red)}

/* header */
.top-strip{left:0;top:0;width:1200px;height:34px;background:linear-gradient(#2b2620,#4a4238)}
.nav-bar{left:0;top:34px;width:1200px;height:56px;background:var(--white);box-shadow:0 1px 3px rgba(0,0,0,.15)}
.nav-link{top:34px;height:56px;line-height:56px;font-family:"Exo",Arial,sans-serif;font-size:13px;font-weight:500;color:var(--ink);text-transform:uppercase}
.nav-link.active{color:var(--red);border-bottom:3px solid var(--red);padding:0 16px;line-height:53px}
.brand-plate{left:540px;top:0;width:120px;height:132px;background:var(--white);border-radius:0 0 60px 60px;box-shadow:0 2px 6px rgba(0,0,0,.25);display:flex;flex-direction:column;align-items:center;justify-content:center;gap:6px}
.brand-plate .dot{width:16px;height:16px;border-radius:50%;background:var(--red)}
.brand-plate .name{font-family:"Exo",Arial,sans-serif;font-weight:700;font-size:15px;color:var(--red);text-align:center;line-height:1.15}

/* hero */
.hero{left:0;top:90px;width:1200px;height:467px;background:radial-gradient(ellipse at 60% 35%,#c9b89a 0%,#7c6b55 35%,#3a3129 70%,#1d1915 100%)}
.hero-arrow{width:42px;height:42px;border-radius:50%;display:flex;align-items:center;justify-content:center}
.hero-arrow.prev{left:67px;top:282px;border:2px solid var(--white)}
.hero-arrow.next{left:1090px;top:282px;border:2px solid var(--red)}
.hero-badge{left:161px;top:333px;width:110px;height:110px;display:flex;flex-direction:column;align-items:center;justify-content:center;gap:6px}
.hero-badge .dot{width:22px;height:22px;border-radius:50%;background:var(--red)}
.hero-badge .name{font-family:"Exo",Arial,sans-serif;font-weight:700;font-size:14px;color:var(--red);text-align:center;line-height:1.15}
.hero-title{left:292px;top:325px;font-size:44px;color:var(--red);font-weight:600;letter-spacing:1px}
.hero-text{left:294px;top:378px;width:340px;font-size:14px;line-height:20px;color:var(--white)}

/* welcome */
.welcome{left:0;top:557px;width:1200px;height:274px;background:var(--light-bg)}
.welcome-title{left:161px;top:590px;font-size:41px;line-height:44px;color:var(--ink);font-weight:400}
.register-btn{left:161px;top:700px;width:285px;height:85px;background:linear-gradient(#e52129,var(--red-dark));padding:14px 0 0 78px;color:var(--white)}
.register-btn .season{font-family:"Exo",Arial,sans-serif;font-size:15px;letter-spacing:1px;font-variant:small-caps}
.register-btn .cta{font-family:"Exo",Arial,sans-serif;font-size:22px;font-weight:500;text-transform:uppercase;letter-spacing:.5px;margin-top:2px}
.talk-title{left:480px;top:594px;font-size:28px;line-height:32px;font-weight:400;letter-spacing:1px}
.talk-rule{left:480px;top:672px;width:288px;height:2px;background:var(--line)}
.talk-text{left:480px;top:686px;width:285px;font-size:14px;line-height:18.6px;color:var(--grey-text)}
.notice{left:804px;top:585px;width:235px;height:218px;background:var(--white);border:1px solid #cfcfcf;text-align:center}
.notice-art{margin:10px auto 0;width:215px;height:96px;background:linear-gradient(#f5f5f5,#e2e2e2);display:flex;align-items:center;justify-content:center}
.notice-head{font-family:"Exo",Arial,sans-serif;font-weight:700;font-size:27px;color:var(--red);line-height:30px;margin-top:4px}
.notice-text{font-size:12.5px;line-height:16px;color:#444;margin:2px 14px 0}
.notice-btn{display:inline-block;margin-top:9px;background:var(--yellow);border:2px solid #c59d00;border-radius:12px;padding:3px 14px;font-size:9px;font-weight:700;text-transform:uppercase;color:#333}

/* fixtures */
.fixtures-title{left:161px;top:882px;font-size:32px;font-weight:500;letter-spacing:1px}
.fixtures-title .amp{color:var(--ink)}
.fixtures-rule{left:161px;top:937px;width:626px;height:2px;background:var(--line)}
.fixtures-text{left:161px;top:956px;width:620px;font-size:13.5px;line-height:20px;color:var(--grey-text)}
.fixture-list{list-style:none;font-family:"Exo",Arial,sans-serif;font-size:15px;text-transform:uppercase;color:#333}
.fixture-list li{height:25.7px;line-height:25.7px;display:flex;align-items:center}
.fixture-list li::before{content:"";width:7px;height:7px;border:1.5px solid #444;margin-right:13px;flex:none}
.fixture-list li.current{color:var(--red)}
.fixture-list li.current::before{border-color:var(--red)}
.player-photo{left:830px;top:859px;width:210px;height:496px;background:linear-gradient(#c81d2a,#8e1018 60%,#5a0a0f);border-radius:90px 90px 10px 10px}

/* sponsors */
.sponsors{left:0;top:1355px;width:1200px;height:619px;background:var(--light-bg)}
.sponsors-title{left:0;top:1420px;width:1200px;text-align:center;font-size:30px;font-weight:400;letter-spacing:1.5px}
.sponsor{width:211px;height:117px;display:flex;align-items:center;justify-content:center;gap:8px;font-family:"Open Sans",Arial,sans-serif;font-weight:600;font-size:16px;text-align:center;padding:0 10px}
.sponsor .mark{width:12px;height:12px;flex:none}
.s-light{background:var(--white);color:#333}
.s-brown{background:#6b3a0c;color:#f3e6d4}
.s-black{background:#1a1a1a;color:#eee}
.s-grey{background:#c9ccd0;color:#1f4f8a}
.s-blue{background:#0d4fa8;color:var(--yellow)}

/* footer */
.footer{left:0;top:1974px;width:1200px;height:349px;background:var(--footer-bg)}
.foot-head{top:2026px;font-size:15px;color:var(--red);font-weight:400;letter-spacing:.5px}
.foot-rule{top:2055px;height:1px;background:#444}
.site-map{left:161px;top:2072px;list-style:none;font-size:12.5px;color:var(--footer-text)}
.site-map li{height:26px;line-height:26px;display:flex;align-items:center}
.site-map li::before{content:"";width:7px;height:7px;border:1.5px solid #9a9a9a;margin-right:13px}
.site-map li.current{color:var(--yellow)}
.site-map li.current::before{border-color:var(--yellow)}
.news-arrow{top:2029px;width:14px;height:14px;border-radius:50%}
.news-item{left:410px;width:300px;display:flex;gap:12px}
.news-thumb{width:58px;height:38px;background:linear-gradient(#6b6b6b,#3a3a3a);flex:none}
.news-title{font-size:11.5px;font-weight:700;color:#e8e8e8;line-height:14px}
.news-date{font-size:9.5px;font-style:italic;color:#8d8d8d;margin-top:2px}
.view-all{left:983px;top:2029px;width:54px;height:15px;border-radius:8px;background:var(--yellow);font-size:8px;font-weight:700;color:#333;text-align:center;line-height:15px}
.gallery{left:778px;top:2079px;width:259px;height:164px;display:grid;grid-template-columns:repeat(3,1fr);grid-template-rows:repeat(3,1fr);gap:3px}
.gallery div{background:linear-gradient(135deg,#b52a2a,#5e5650)}
.gallery div:nth-child(even){background:linear-gradient(135deg,#7b7368,#3b3632)}
.gallery .tall{grid-row:span 2}
.bottom-rule{left:161px;top:2271px;width:878px;height:1px;background:#3a3a3a}
.copyright{left:161px;top:2289px;font-size:9.5px;color:#777}
.social{top:2284px;width:27px;height:27px;border-radius:50%;border:1.5px solid #777}
.social.first{border-color:#2b8fd6}
</style>
</head>
<body>

<header>
  <div class="abs top-strip"></div>
  <div class="abs nav-bar"></div>
  <nav>
    <a class="abs nav-link active" style="left:162px">Home</a>
    <a class="abs nav-link" style="left:241px">About Us</a>
    <a class="abs nav-link" style="left:328px">News</a>
    <a class="abs nav-link" style="left:390px">Fixture &amp; Results</a>
    <a class="abs nav-link" style="left:686px">Photo Gallery</a>
    <a class="abs nav-link" style="left:808px">Sponsor</a>
    <a class="abs nav-link" style="left:892px">Club</a>
    <a class="abs nav-link" style="left:949px">Contact Us</a>
  </nav>
  <div class="abs brand-plate">
    <span class="dot"></span>
    <span class="name">TAVENHURST<br>FC</span>
  </div>
</header>

<section>
  <div class="abs hero" role="img" aria-label="Action photo of footballers in a stadium, a player striking the ball towards a diving goalkeeper"></div>
  <div class="abs hero-arrow prev">
    <svg width="14" height="14" viewBox="0 0 14 14"><path d="M9 2 L4 7 L9 12" fill="none" stroke="#fff" stroke-width="2"/></svg>
  </div>
  <div class="abs hero-arrow next">
    <svg width="14" height="14" viewBox="0 0 14 14"><path d="M5 2 L10 7 L5 12" fill="none" stroke="#d0121b" stroke-width="2"/></svg>
  </div>
  <div class="abs hero-badge">
    <span class="dot"></span>
    <span class="name">TAVENHURST<br>FC</span>
  </div>
  <h1 class="abs heading hero-title">Tavenhurst FC</h1>
  <p class="abs hero-text">Lorem Ipsum is simply dummy text of the printing and typesetting industry. Lorem Ipsum has been the industry's standard dummy text .</p>
</section>

<section>
  <div class="abs welcome"></div>
  <h2 class="abs heading welcome-title">Welcome to<br><span class="red">Tavenhurst FC</span></h2>
  <a class="abs register-btn">
    <div class="season">2014 Season</div>
    <div class="cta">Register Online</div>
  </a>
  <h2 class="abs heading talk-title">Let's talk <span class="red">about</span><br>Tavenhurst FC.</h2>
  <div class="abs talk-rule"></div>
  <p class="abs talk-text">Lorem Ipsum is simply dummy text of the printing and typesetting industry. Lorem Ipsum has been the industry's standard dummy text ever since the 1500s, when an unknown printer took a galley of type and scrambled it to make a type specimen.</p>
  <aside class="abs notice">
    <div class="notice-art" role="img" aria-label="No smoking sign beside an ashtray">
      <svg width="64" height="64" viewBox="0 0 64 64"><circle cx="32" cy="32" r="27" fill="#fff" stroke="#111" stroke-width="6"/><line x1="13" y1="13" x2="51" y2="51" stroke="#111" stroke-width="6"/></svg>
    </div>
    <div class="notice-head">NO SMOKING</div>
    <p class="notice-text">There is a No Smoking Ban for all Sports Grounds</p>
    <span class="notice-btn">Find out more</span>
  </aside>
</section>

<section>
  <h2 class="abs heading fixtures-title red">Fixtures <span class="amp">&amp;</span> Results</h2>
  <div class="abs fixtures-rule"></div>
  <p class="abs fixtures-text">Lorem Ipsum is simply dummy text of the printing and typesetting industry. Lorem Ipsum has been the industry's standard dummy text ever since the 1500s, when an unknown printer took a galley of type and scrambled it to make a type specimen book.</p>
  <ul class="abs fixture-list" style="left:161px;top:1047px">
    <li>Premier League</li><li class="current">Premier League Res</li><li>Super League</li><li>Super League Res</li><li>Under 16 / 2</li><li>Under 17 / 1</li><li>Under 10 / 2</li><li>Under 10 / 3</li><li>Under 11 / 1</li><li>Under 12 / 3</li>
  </ul>
  <ul class="abs fixture-list" style="left:424px;top:1047px">
    <li>Under 13 / 3</li><li>Under 14 / 3</li><li>AA Men / 5</li><li>AA Men / 6</li><li>AA Men / 8</li><li>AA Men / 10</li><li>AA Men / 10</li><li>AA Men / 14</li><li>07 ECL / Red</li><li>07 ECL / Green</li>
  </ul>
  <ul class="abs fixture-list" style="left:644px;top:1047px">
    <li>07 ECL / Blue</li><li>08 ECL / Blue</li><li>08 ECL / Green</li><li>09 / Green</li><li>06 / A Green</li><li>06 / B Blue</li><li>06 / C Red</li><li>06 / D Purple</li><li>06 / E White</li><li>06 / F Brown</li>
  </ul>
  <div class="abs player-photo" role="img" aria-label="Club player in a red kit standing with arms folded beside a football"></div>
</section>

<section>
  <div class="abs sponsors"></div>
  <h2 class="abs heading sponsors-title">Tavenhurst <span class="red">FC</span> Sponsor's</h2>
  <div class="abs sponsor s-light" style="left:161px;top:1512px"><span class="mark" style="background:#f39a1e"></span>Brightframe Media</div>
  <div class="abs sponsor s-brown" style="left:383px;top:1512px">Orvello Ristorante</div>
  <div class="abs sponsor s-black" style="left:605px;top:1512px">Velmont Motors</div>
  <div class="abs sponsor s-light" style="left:828px;top:1512px;color:#9c1c2e">Dorian Keswick &amp; Co</div>
  <div class="abs sponsor s-grey" style="left:161px;top:1641px">Tidemark Seal</div>
  <div class="abs sponsor s-light" style="left:383px;top:1641px">Kelby Hill Trophies</div>
  <div class="abs sponsor s-light" style="left:605px;top:1641px;color:#9c1c2e">Vantorel</div>
  <div class="abs sponsor s-blue" style="left:828px;top:1641px">Harlow Motor Group</div>
  <div class="abs sponsor s-light" style="left:383px;top:1771px;color:#1f4f8a"><span class="mark" style="background:#f3c500;border-radius:50%"></span>Harbour Bowls Club</div>
  <div class="abs sponsor s-light" style="left:605px;top:1771px;color:#1d6b3a">Corvane Bank</div>
</section>

<footer>
  <div class="abs footer"></div>

  <h3 class="abs heading foot-head" style="left:161px">Site Map</h3>
  <div class="abs foot-rule" style="left:161px;width:185px"></div>
  <ul class="abs site-map">
    <li>Become A Referee</li><li>News</li><li>Fixture &amp; Results</li><li class="current">Photo Gallery</li><li>Sponsor</li><li>Club</li><li>Contact Us</li>
  </ul>

  <h3 class="abs heading foot-head" style="left:410px">Latest News</h3>
  <span class="abs news-arrow" style="left:669px;background:#777"></span>
  <span class="abs news-arrow" style="left:688px;background:var(--yellow)"></span>
  <div class="abs foot-rule" style="left:410px;width:296px"></div>
  <div class="abs news-item" style="top:2082px"><div class="news-thumb" role="img" aria-label="Match photo"></div><div><div class="news-title">Lorem Ipsum is simply dummy text of the typesetting industry.</div><div class="news-date">Mar 11, 2014</div></div></div>
  <div class="abs news-item" style="top:2141px"><div class="news-thumb" role="img" aria-label="Match photo"></div><div><div class="news-title">Lorem Ipsum is simply dummy text of the typesetting industry.</div><div class="news-date">Mar 11, 2014</div></div></div>
  <div class="abs news-item" style="top:2198px"><div class="news-thumb" role="img" aria-label="Match photo"></div><div><div class="news-title">Lorem Ipsum is simply dummy text of the typesetting industry.</div><div class="news-date">Mar 11, 2014</div></div></div>

  <h3 class="abs heading foot-head" style="left:777px">Photo Gallery</h3>
  <span class="abs view-all">View All</span>
  <div class="abs foot-rule" style="left:777px;width:260px"></div>
  <div class="abs gallery" role="img" aria-label="Grid of club photos: players, team groups and supporters">
    <div class="tall"></div><div></div><div></div><div class="tall"></div><div></div><div></div><div></div>
  </div>

  <div class="abs bottom-rule"></div>
  <p class="abs copyright">Copyright TAVENHURST FC © 2014. All rights reserved. Terms and Conditions</p>
  <span class="abs social first" style="left:888px" aria-label="Social link"></span>
  <span class="abs social" style="left:919px" aria-label="Social link"></span>
  <span class="abs social" style="left:950px" aria-label="Social link"></span>
  <span class="abs social" style="left:981px" aria-label="Social link"></span>
  <span class="abs social" style="left:1012px" aria-label="Social link"></span>
</footer>

</body>
</html>
```